Business Card Design for Occupational Medicine Start Up Company

We need to design a professional business card. We are a healthcare company providing occupational medicine services to blue collar industries. We are professional, efficient and high quality service providers.

Target Market(s)

Blue Collar Industry: Shipbuilding, Ports, Trucking Companies; The Executives and Safety Officers for these companies

Industry/Entity Type

Healthcare

Contact Information for Business Card

Logo, Name, Title, Email, Phone

Other font styles liked:
• Please match our Brand Guide

Requirements
Must have
• Our Company Colors and Logo

```html
<!DOCTYPE html>
<html lang="en">
<head>
<meta charset="utf-8">
<title>ShiftWell Clinics – Business Card</title>
<link href="https://fonts.googleapis.com/css2?family=Montserrat:wght@400;500;600&display=swap" rel="stylesheet">
<style>
  :root {
    --stage: #2a2a2a;
    --paper: #f7f7f5;
    --navy: #2e2f7a;
    --sky: #2f9bd6;
    --gold: #e9a23b;
    --ink-soft: #3b3d6e;
  }
  * { box-sizing: border-box; margin: 0; padding: 0; }
  html, body { width: 1200px; height: 1200px; overflow: hidden; }
  body {
    background: var(--stage);
    font-family: "Montserrat", Arial, sans-serif;
    position: relative;
  }
  .card {
    position: absolute;
    width: 594px;
    height: 348px;
    background: var(--paper);
    border-radius: 22px;
    overflow: hidden;
  }
  .card-front { left: 298px; top: 200px; }
  .card-back  { left: 292px; top: 637px; }

  .brand-dot {
    position: absolute;
    width: 52px; height: 52px;
    border-radius: 50%;
    background: var(--navy);
  }
  .wordmark {
    position: absolute;
    color: var(--navy);
    font-weight: 600;
    text-align: center;
    line-height: 1;
  }
  .wordmark .line-main { display: block; letter-spacing: 0.5px; }
  .wordmark .line-sub  { display: block; letter-spacing: 6px; }

  .card-front .brand-dot { left: 271px; top: 100px; }
  .card-front .wordmark { left: 0; width: 100%; top: 178px; }
  .card-front .line-main { font-size: 36px; }
  .card-front .line-sub  { font-size: 17px; margin-top: 8px; }

  .site-url {
    position: absolute;
    left: 0; width: 100%;
    top: 301px;
    text-align: center;
    font-size: 16px;
    letter-spacing: 1px;
    color: var(--navy);
  }
  .site-url .accent-sky { color: var(--sky); }
  .site-url .accent-gold { color: var(--gold); }

  .card-back .brand-dot { left: 134px; top: 100px; }
  .card-back .wordmark { left: 30px; width: 260px; top: 178px; }
  .card-back .line-main { font-size: 28px; }
  .card-back .line-sub  { font-size: 14px; margin-top: 6px; letter-spacing: 5px; }

  .person { position: absolute; left: 316px; top: 68px; }
  .person-name {
    font-size: 25px; font-weight: 600; color: var(--sky); letter-spacing: 0.5px;
  }
  .person-title {
    font-size: 16px; color: var(--ink-soft); margin-top: 2px;
  }
  .contact-list {
    position: absolute; left: 316px; top: 136px;
    list-style: none;
    font-size: 15.5px; color: var(--navy);
  }
  .contact-list li {
    display: flex; align-items: center; gap: 12px; height: 21.5px;
  }
  .contact-list svg { width: 14px; height: 14px; flex: none; }
  .address {
    position: absolute; left: 316px; top: 216px;
    display: flex; gap: 12px;
    font-size: 15.5px; color: var(--navy); line-height: 22px;
  }
  .address svg { width: 14px; height: 16px; margin-top: 3px; flex: none; }

  .stripe { position: absolute; left: 0; width: 100%; }
  .stripe-sky  { top: 322px; height: 7px; background: var(--sky); }
  .stripe-navy { top: 332px; height: 6px; background: var(--navy); }
  .stripe-gold { top: 341px; height: 7px; background: var(--gold); }
</style>
</head>
<body>

  <section class="card card-front" aria-label="Business card front">
    <span class="brand-dot" aria-hidden="true"></span>
    <div class="wordmark">
      <span class="line-main">SHIFTWELL</span>
      <span class="line-sub">CLINICS</span>
    </div>
    <p class="site-url">www.<span class="accent-sky">shiftwell</span><span class="accent-gold">clinics</span>.com</p>
  </section>

  <section class="card card-back" aria-label="Business card back">
    <span class="brand-dot" aria-hidden="true"></span>
    <div class="wordmark">
      <span class="line-main">SHIFTWELL</span>
      <span class="line-sub">CLINICS</span>
    </div>

    <div class="person">
      <p class="person-name">DANIEL REYES</p>
      <p class="person-title">Senior Doctor</p>
    </div>

    <ul class="contact-list">
      <li>
        <svg viewBox="0 0 16 16" aria-hidden="true"><path fill="var(--sky)" d="M3 2h3l1.5 3.5-2 1.3a9 9 0 0 0 3.7 3.7l1.3-2L14 10v3a1 1 0 0 1-1 1A12 12 0 0 1 2 3a1 1 0 0 1 1-1z"/></svg>
        555-014-2290
      </li>
      <li>
        <svg viewBox="0 0 16 16" aria-hidden="true"><rect x="1" y="3" width="14" height="10" rx="1" fill="var(--navy)"/><path d="M1.5 3.5 8 9l6.5-5.5" stroke="var(--paper)" stroke-width="1.4" fill="none"/></svg>
        dreyes@shiftwellclinics.com
      </li>
      <li>
        <svg viewBox="0 0 16 16" aria-hidden="true"><g fill="none" stroke="var(--gold)" stroke-width="1.3"><circle cx="8" cy="8" r="6.3"/><ellipse cx="8" cy="8" rx="2.8" ry="6.3"/><path d="M1.7 8h12.6M2.6 5h10.8M2.6 11h10.8"/></g></svg>
        www.shiftwellclinics.com
      </li>
    </ul>

    <div class="address">
      <svg viewBox="0 0 14 18" aria-hidden="true"><path fill="var(--gold)" d="M7 0a7 7 0 0 1 7 7c0 5-7 11-7 11S0 12 0 7a7 7 0 0 1 7-7zm0 4a3 3 0 1 0 0 6 3 3 0 0 0 0-6z"/></svg>
      <p>48 Harbor Road, Suite 210<br>Port Alden, State 24680</p>
    </div>

    <span class="stripe stripe-sky"></span>
    <span class="stripe stripe-navy"></span>
    <span class="stripe stripe-gold"></span>
  </section>

</body>
</html>
```